Business Card Design using new attached logo

We are a family run Plumbing and Heating firm looking to improve our company image with an improved business card and new logo.We are looking to keep the company colour (Blue) involved in our design

Reason: New logo added which needs to be incorporated on designs

Industry/Entity Type

Business

Contact Information for Business Card

See attachment of all info required.

Requirements
Must have
• We have just picked a new company logo which is attached.
• Could you please provide your business card designs using this logo.
• We are looking for the logo on the back as well as the front with all the info required

```html
<!DOCTYPE html>
<html lang="en">
<head>
<meta charset="utf-8">
<title>Vale Services – Business Card</title>
<link href="https://fonts.googleapis.com/css2?family=Open+Sans:wght@400;600&family=Noto+Serif:wght@400&family=Cousine:wght@400&display=swap" rel="stylesheet">
<style>
  :root {
    --backdrop: #e8e3da;
    --card: #ffffff;
    --navy: #0a1a7c;
    --bright-blue: #1c86f2;
    --text-light: #ffffff;
    --shadow: rgba(0, 0, 0, 0.28);
  }
  * { box-sizing: border-box; margin: 0; padding: 0; }
  html, body {
    width: 1200px;
    height: 801px;
    overflow: hidden;
    background: var(--backdrop);
  }
  .canvas {
    position: relative;
    width: 1200px;
    height: 801px;
  }
  .card {
    position: absolute;
    top: 240px;
    width: 520px;
    height: 320px;
    background: var(--card);
    overflow: hidden;
    box-shadow: 0 8px 22px var(--shadow);
  }
  .card--front { left: 50px; }
  .card--back { left: 630px; }

  /* Front */
  .front__side-panel {
    position: absolute;
    top: 28px;
    right: 0;
    width: 160px;
    height: 292px;
    background: var(--navy);
    border-top-left-radius: 14px;
  }
  .front__bottom-band {
    position: absolute;
    left: 0;
    right: 0;
    bottom: 0;
    height: 72px;
    background: var(--navy);
  }
  .front__white-field {
    position: absolute;
    left: 0;
    top: 0;
    width: 382px;
    height: 248px;
    background: var(--card);
    border-bottom-right-radius: 18px;
  }
  .brand-name {
    font-family: "Open Sans", sans-serif;
    font-weight: 600;
    color: var(--navy);
    letter-spacing: 0.5px;
  }
  .front__brand {
    position: absolute;
    left: 48px;
    top: 92px;
    font-size: 34px;
  }
  .name-tag {
    position: absolute;
    left: 280px;
    top: 92px;
    width: 210px;
    height: 74px;
    background: var(--bright-blue);
    color: var(--text-light);
    text-align: center;
    padding-top: 10px;
    box-shadow: -4px 6px 10px var(--shadow);
  }
  .name-tag__name {
    font-family: "Noto Serif", serif;
    font-size: 24px;
    letter-spacing: 1px;
    line-height: 1.1;
  }
  .name-tag__role {
    font-family: "Open Sans", sans-serif;
    font-size: 19px;
    line-height: 1.3;
  }

  /* Back */
  .contact-panel {
    position: absolute;
    left: 62px;
    top: 78px;
    width: 396px;
    height: 130px;
    background: var(--navy);
    border-radius: 12px;
    color: var(--text-light);
    font-family: "Cousine", monospace;
    font-size: 12.5px;
    line-height: 1.45;
    text-align: center;
    display: flex;
    flex-direction: column;
    justify-content: center;
  }
  .back__brand {
    position: absolute;
    left: 0;
    right: 0;
    top: 236px;
    text-align: center;
    font-size: 30px;
  }
</style>
</head>
<body>
  <main class="canvas">
    <section class="card card--front" aria-label="Business card front">
      <div class="front__side-panel"></div>
      <div class="front__bottom-band"></div>
      <div class="front__white-field"></div>
      <div class="brand-name front__brand">Vale Services</div>
      <div class="name-tag">
        <div class="name-tag__name">MARK ELDEN</div>
        <div class="name-tag__role">Director</div>
      </div>
    </section>

    <section class="card card--back" aria-label="Business card back">
      <div class="contact-panel">
        <p>12 ALDER PARADE,</p>
        <p>MARSH ROAD, LINDFORD, SURREY LF2 7QT</p>
        <p>Telephone: 020 7946 0321 Fax: 020 7946 0322</p>
        <p>Mobile: 07700 900412</p>
        <p>markelden@valeservicesltd.co.uk</p>
      </div>
      <div class="brand-name back__brand">Vale Services</div>
    </section>
  </main>
</body>
</html>
```